Elegant Business Card for Technology Company

Client is a supplier of innovative industrial communications and automation equipment since 2002. This contest is to gather fresh ideas for a redesign of the existing business card. Client is looking for design that best communicates tagline "Industrial Networking and Computing Specialist".

Design submissions should look modern, clean, elegant and professional. It should not be cluttered. Use white as the primary colour. Orange and black as secondary colour. Refer to jpeg File 1 on the current design.

Fonts used by Client used include Arial Regular, Arial Black, Roboto Regular, Roboto Black and Lato.

The winning design will be sent for offset printing using super white 250gsm artcard paper (open for suggestions).

Target Market(s)

System Engineers, Project Managers, Purchasing Managers from companies providing engineering services for Smart Cities.

Industry/Entity Type

Information Technology

Contact Information for Business Card

Refer to PDF File 3 for Business Card Details. Priority of short contact information would be as follows Name > Job Title > Email > Mobile > Web > Tel > Fax > Business Address >UEN (UEN represents company registration number)

Font styles to use
Sans Serif

Colors
ffffff
f37122
000000
5c5c5c

Requirements
Must have
• Refer to AI File 2 (Company Logo) & PDF File 3 (Information on Namecard)
Should not have
• No QR codes
• No Social Media Icons
• Do not create full Black or Orange colour background

```html
<!DOCTYPE html>
<html lang="en">
<head>
<meta charset="utf-8">
<title>KVN Business Card</title>
<link rel="stylesheet" href="https://fonts.googleapis.com/css2?family=Open+Sans:wght@400;600;800&display=swap">
<style>
  :root {
    --white: #ffffff;
    --orange: #f37122;
    --black: #000000;
    --grey: #5c5c5c;
    --divider: #c9c9c9;
    --backdrop: #ececec;
    --peach-soft: #fdf1e9;
  }
  * { box-sizing: border-box; margin: 0; padding: 0; }
  html, body {
    width: 1105px;
    height: 1200px;
    overflow: hidden;
    background: var(--backdrop);
    font-family: "Open Sans", Arial, sans-serif;
  }
  .card {
    position: absolute;
    left: 112px;
    width: 880px;
    height: 500px;
    background: var(--white);
    overflow: hidden;
  }
  .card--front { top: 70px; }
  .card--back { top: 630px; }

  /* Front */
  .brand {
    position: absolute;
    left: 95px;
    top: 150px;
    display: flex;
    align-items: center;
    gap: 16px;
  }
  .brand__dot {
    width: 48px;
    height: 48px;
    border-radius: 50%;
    background: var(--orange);
  }
  .brand__name {
    font-size: 125px;
    font-weight: 800;
    line-height: 1;
    color: var(--black);
  }
  .divider {
    position: absolute;
    left: 469px;
    top: 70px;
    width: 1px;
    height: 325px;
    background: var(--divider);
  }
  .contact {
    position: absolute;
    left: 500px;
    top: 74px;
    color: var(--grey);
  }
  .contact__name {
    font-size: 32px;
    font-weight: 600;
    color: var(--orange);
    line-height: 1.1;
  }
  .contact__title {
    font-size: 24px;
    color: #222;
    line-height: 1.3;
    margin-bottom: 14px;
  }
  .contact__address {
    font-size: 22px;
    line-height: 31px;
    margin-left: 6px;
    margin-bottom: 10px;
  }
  .contact__list { list-style: none; margin-left: 6px; }
  .contact__item {
    display: flex;
    align-items: center;
    gap: 14px;
    font-size: 22px;
    line-height: 34px;
  }
  .contact__icon { width: 20px; height: 20px; fill: var(--orange); flex: none; }
  .swoosh { position: absolute; left: 0; bottom: 0; width: 880px; height: 500px; }
  .web {
    position: absolute;
    left: 0;
    right: 0;
    bottom: 10px;
    text-align: center;
    color: var(--white);
    font-size: 21px;
    letter-spacing: 0.28em;
  }

  /* Back */
  .backdrop-fill {
    position: absolute;
    inset: 0;
    background: linear-gradient(135deg, var(--peach-soft) 0%, var(--white) 45%, var(--white) 60%, var(--peach-soft) 100%);
  }
  .back-brand {
    position: absolute;
    left: 0;
    right: 0;
    top: 110px;
    text-align: center;
    font-size: 150px;
    font-weight: 800;
    line-height: 1;
    color: var(--black);
  }
  .tagline {
    position: absolute;
    left: 0;
    right: 0;
    top: 340px;
    text-align: center;
    font-size: 24px;
    line-height: 31px;
    color: var(--grey);
  }
</style>
</head>
<body>

<section class="card card--front">
  <div class="brand">
    <span class="brand__dot"></span>
    <span class="brand__name">KVN</span>
  </div>

  <div class="divider"></div>

  <div class="contact">
    <p class="contact__name">Daniel Lim</p>
    <p class="contact__title">Sales Manager</p>
    <p class="contact__address">22 Rowell Park Loop<br>#05-12 (Block B)<br>Singapore 417390</p>
    <ul class="contact__list">
      <li class="contact__item">
        <svg class="contact__icon" viewBox="0 0 24 24"><path d="M6.6 10.8a15 15 0 0 0 6.6 6.6l2.2-2.2a1 1 0 0 1 1-.25 11.4 11.4 0 0 0 3.6.57 1 1 0 0 1 1 1V20a1 1 0 0 1-1 1A17 17 0 0 1 3 4a1 1 0 0 1 1-1h3.5a1 1 0 0 1 1 1c0 1.25.2 2.45.57 3.57a1 1 0 0 1-.25 1z"/></svg>
        +65 6123 4501
      </li>
      <li class="contact__item">
        <svg class="contact__icon" viewBox="0 0 24 24"><path d="M7 1h10a2 2 0 0 1 2 2v18a2 2 0 0 1-2 2H7a2 2 0 0 1-2-2V3a2 2 0 0 1 2-2zm0 3v14h10V4zm5 15.2a1.2 1.2 0 1 0 0 2.4 1.2 1.2 0 0 0 0-2.4z"/></svg>
        +65 9012 3456
      </li>
      <li class="contact__item">
        <svg class="contact__icon" viewBox="0 0 24 24"><path d="M6 2h10l2 2v5H6zM3 10h18a2 2 0 0 1 2 2v7H1v-7a2 2 0 0 1 2-2zm3 6v6h12v-6z"/></svg>
        +65 6123 4502
      </li>
      <li class="contact__item">
        <svg class="contact__icon" viewBox="0 0 24 24"><path d="M2 5h20v14H2zm2 2v.5l8 5 8-5V7zm0 2.9V17h16V9.9l-8 5z"/></svg>
        sales@kvn.com.sg
      </li>
    </ul>
  </div>

  <svg class="swoosh" viewBox="0 0 880 500" aria-hidden="true">
    <path d="M0,468 Q440,420 880,468 L880,500 L0,500 Z" fill="var(--orange)"/>
    <path d="M0,466 Q440,400 880,466 Q440,418 0,466 Z" fill="var(--black)"/>
  </svg>
  <p class="web">www.kvn.com.sg</p>
</section>

<section class="card card--back">
  <div class="backdrop-fill" role="img" aria-label="Faint peach decorative pattern across the card background"></div>
  <p class="back-brand">KVN</p>
  <p class="tagline">
    Industrial Networking &amp; Computing Specialist<br>
    Industrial Ethernet / Wireless / Cellular<br>
    Industrial &amp; Embedded Computing / Serial / Fieldbus Connectivity<br>
    IP Video Surveillance / Remote Automation
  </p>
</section>

</body>
</html>
```